business card deign

Logo needs the following on it.
1. attached logo
2. Tagline - "If it chills the glass or lifts the whole room...we bring it!"
3. Name- Dalton Pikes, Founder and CPO
4. Address - 412 E. Carver Avenue, Ste 2207, Tampa, FL. 33917
5. Phone - 555.318.4726

```html
<!DOCTYPE html>
<html lang="en">
<head>
<meta charset="utf-8">
<title>Hopwell Business Card</title>
<link rel="stylesheet" href="https://fonts.googleapis.com/css2?family=Montserrat:wght@400;500;700&display=swap">
<style>
  :root {
    --backdrop: #8c8c8c;
    --card-dark: #1c1c1c;
    --card-light: #ffffff;
    --ink: #111111;
    --ink-soft: #2a2a2a;
    --tagline: #d6d6d6;
    --logo-on-dark: #060606;
  }
  * { box-sizing: border-box; margin: 0; padding: 0; }
  html, body {
    width: 1200px; height: 900px; overflow: hidden;
    background: var(--backdrop);
    font-family: "Montserrat", sans-serif;
  }
  .canvas { position: relative; width: 1200px; height: 900px; }
  .card {
    position: absolute; width: 630px; height: 360px;
    box-shadow: 0 6px 18px rgba(0,0,0,0.35);
  }
  .card--front { left: 90px; top: 60px; background: var(--card-dark); }
  .card--back { left: 480px; top: 480px; background: var(--card-light); color: var(--ink); }

  .brand { display: flex; align-items: center; gap: 14px; }
  .brand__dot { width: 16px; height: 16px; border-radius: 50%; flex: none; }
  .brand__name { font-weight: 700; font-size: 34px; letter-spacing: 14px; white-space: nowrap; }

  .card--front .brand {
    position: absolute; left: 0; right: 0; top: 130px; justify-content: center;
  }
  .card--front .brand__name { color: var(--logo-on-dark); }
  .card--front .brand__dot { background: var(--logo-on-dark); }

  .tagline {
    position: absolute; left: 0; right: 0; bottom: 70px; text-align: center;
    color: var(--tagline); font-size: 14px; font-weight: 400; letter-spacing: 0.3px;
  }

  .person { position: absolute; left: 40px; top: 70px; }
  .person__name { font-weight: 700; font-size: 24px; }
  .person__role { font-size: 14px; font-weight: 400; color: var(--ink-soft); margin-top: 2px; }

  .card--back .brand { position: absolute; right: 40px; top: 110px; }
  .card--back .brand__name { color: var(--ink); font-size: 30px; letter-spacing: 11px; }
  .card--back .brand__dot { background: var(--ink); }

  .address {
    position: absolute; right: 40px; top: 180px; text-align: right;
    font-size: 14px; line-height: 1.35; color: var(--ink-soft);
  }

  .contacts { position: absolute; left: 40px; bottom: 36px; list-style: none; }
  .contacts li {
    display: flex; align-items: center; gap: 10px;
    font-size: 15px; line-height: 1.7; color: var(--ink-soft);
  }
  .contacts svg { width: 14px; height: 14px; fill: var(--ink); flex: none; }
</style>
</head>
<body>
<main class="canvas">
  <section class="card card--front">
    <div class="brand">
      <span class="brand__dot"></span>
      <span class="brand__name">HOPWELL</span>
    </div>
    <p class="tagline">If it chills the glass or lifts the whole room...we bring it</p>
  </section>

  <section class="card card--back">
    <div class="person">
      <h1 class="person__name">Dalton Pikes</h1>
      <p class="person__role">Founder and CPO</p>
    </div>

    <div class="brand">
      <span class="brand__dot"></span>
      <span class="brand__name">HOPWELL</span>
    </div>

    <p class="address">412 E. Carver Avenue, Ste 2207,<br>Tampa, FL. 33917</p>

    <ul class="contacts">
      <li>
        <svg viewBox="0 0 24 24" aria-hidden="true"><path d="M6.6 10.8a15.1 15.1 0 0 0 6.6 6.6l2.2-2.2c.3-.3.7-.4 1-.2 1.1.4 2.3.6 3.6.6.6 0 1 .4 1 1V20c0 .6-.4 1-1 1A17 17 0 0 1 3 4c0-.6.4-1 1-1h3.5c.6 0 1 .4 1 1 0 1.3.2 2.5.6 3.6.1.3 0 .7-.2 1z"/></svg>
        555.318.4726
      </li>
      <li>
        <svg viewBox="0 0 24 24" aria-hidden="true"><path d="M2 5h20v14H2z M2 5l10 8 10-8" stroke="#fff" stroke-width="1.5"/></svg>
        info@hopwell.com
      </li>
      <li>
        <svg viewBox="0 0 24 24" aria-hidden="true"><circle cx="12" cy="12" r="10"/><path d="M2 12h20M12 2c3 3 3 17 0 20M12 2c-3 3-3 17 0 20" stroke="#fff" stroke-width="1.4" fill="none"/></svg>
        www.hopwell.com
      </li>
    </ul>
  </section>
</main>
</body>
</html>
```